Tolbek cards

I want a simple business card that pops.
Logo on one side.
On side two i want.
"Are you thinking about a new building on your property, or renovating an existing structure? Contact".....
Owners Name: Dale Whitacre
Owners Phone number: 610-555-0187
Address:4076 Copper Ridge RD, Elmbrook, PA 16999
Committed to Quality, Service, and Integrity

```html
<!DOCTYPE html>
<html lang="en">
<head>
<meta charset="UTF-8">
<title>Tolbek Builders LLC – Business Card</title>
<link rel="stylesheet" href="https://fonts.googleapis.com/css2?family=Inter:ital,wght@0,400;0,700;1,700&display=swap">
<style>
  :root {
    --backdrop: #5a5a5a;
    --brown-deep: #553822;
    --brown-mid: #7a6048;
    --brown-light: #9d8a72;
    --logo-brown: #3e2c1c;
    --card-white: #ffffff;
    --text-light: #ffffff;
  }
  * { margin: 0; padding: 0; box-sizing: border-box; }
  html, body {
    width: 1200px;
    height: 1200px;
    overflow: hidden;
    background: var(--backdrop);
    font-family: "Inter", "Helvetica Neue", Arial, sans-serif;
  }
  .canvas {
    position: relative;
    width: 1200px;
    height: 1200px;
  }
  .card {
    position: absolute;
    left: 265px;
    width: 690px;
    height: 394px;
  }
  .card-back {
    top: 158px;
    background: radial-gradient(ellipse 62% 78% at 50% 50%, var(--brown-light) 0%, var(--brown-mid) 55%, var(--brown-deep) 100%);
    color: var(--text-light);
  }
  .card-front {
    top: 651px;
    background: var(--card-white);
    display: flex;
    align-items: center;
    justify-content: center;
  }
  .pitch {
    position: absolute;
    top: 60px;
    left: 0;
    width: 100%;
    text-align: center;
    font-weight: 700;
    font-style: italic;
    font-size: 18.5px;
    line-height: 24px;
  }
  .contact-row {
    position: absolute;
    top: 186px;
    left: 52px;
    display: flex;
    align-items: center;
  }
  .owner-name {
    font-weight: 700;
    font-size: 29px;
    letter-spacing: 0.2px;
    padding-right: 18px;
    white-space: nowrap;
  }
  .divider {
    width: 1px;
    height: 48px;
    background: var(--text-light);
    margin-right: 14px;
  }
  .contact-lines {
    font-size: 15.5px;
    line-height: 24px;
    white-space: nowrap;
  }
  .phone {
    display: flex;
    align-items: center;
    gap: 8px;
  }
  .phone svg { width: 14px; height: 14px; }
  .tagline {
    position: absolute;
    bottom: 36px;
    left: 0;
    width: 100%;
    text-align: center;
    font-size: 17px;
  }
  .brand {
    display: flex;
    align-items: center;
    gap: 18px;
    color: var(--logo-brown);
  }
  .brand-mark {
    width: 62px;
    height: 62px;
    background: var(--logo-brown);
  }
  .brand-name {
    font-weight: 700;
    font-size: 42px;
    letter-spacing: 1px;
  }
</style>
</head>
<body>
<main class="canvas">
  <section class="card card-back" aria-label="Card back with contact details">
    <p class="pitch">Are you thinking about a new building on your property,<br>or renovating an existing structure?</p>
    <div class="contact-row">
      <h1 class="owner-name">DALE WHITACRE</h1>
      <span class="divider"></span>
      <div class="contact-lines">
        <p class="phone">
          <svg viewBox="0 0 24 24" aria-hidden="true"><path fill="#ffffff" d="M6.6 10.8a15.1 15.1 0 0 0 6.6 6.6l2.2-2.2a1 1 0 0 1 1-.25 11.4 11.4 0 0 0 3.6.57 1 1 0 0 1 1 1V20a1 1 0 0 1-1 1A17 17 0 0 1 3 4a1 1 0 0 1 1-1h3.5a1 1 0 0 1 1 1c0 1.25.2 2.45.57 3.57a1 1 0 0 1-.25 1z"/></svg>
          610-555-0187
        </p>
        <p class="address">4076 Copper Ridge RD, Elmbrook, PA 16999</p>
      </div>
    </div>
    <p class="tagline">Committed to Quality, Service, and Integrity</p>
  </section>

  <section class="card card-front" aria-label="Card front with company name">
    <div class="brand">
      <span class="brand-mark"></span>
      <span class="brand-name">TOLBEK BUILDERS LLC</span>
    </div>
  </section>
</main>
</body>
</html>
```